Business Card Design

We like to use greens as you will see in our logo (but not TOO much green). We are a Dental Clinic in a somewhat eccentric community. We do not like the dated sharp designs which we see many dentists use. We're looking for something bright and fresh while still maintaining the integrity of the profession. Elegance is not necessarily what we are going for... we need for the design to be "mature" but also up-lifting.

See our logo.
Updates

Project Deadline Extended
Reason: We have 5 designs which we like. But we'd like to see a few more before committing to a design.

Project Deadline Extended
Reason: We are awaiting revisions to this project. We are still welcoming designs while we wait to see if designers are able to provide to us the revisions we require in order to proceed with a selection.

Target Market(s)

Younger families - ages late 20's to early 40's

Industry/Entity Type

Business

Contact Information for Business Card

Corwel T. Banfry DDS 2730 W. Halvert Rd. Ste. 7 Maple Hollow, OH 48391 (248)555-0174 FX (248)555-0189 info@BrightwellDentalCareMi.com BrigthwellDentalCareMi.com on the back of the card we need an appointment reminder (For____ Date___ Time____) with "If you are unable to keep your appointment, kindly give 48 hours notice" at the bottom. No use of teeth in the design. DOUBLE SIDED DESIGN

Requirements
Should not have
• The use of pictures of teeth

```html
<!DOCTYPE html>
<html lang="en">
<head>
<meta charset="utf-8">
<title>Brightwell Dental Care – Business Card</title>
<link rel="stylesheet" href="https://fonts.googleapis.com/css2?family=Source+Sans+3:ital,wght@0,400;0,600;0,700;1,400&family=Cinzel:wght@600&display=swap">
<style>
  :root{
    --green-dark:#1d6b35;
    --green-light:#7fcd2e;
    --ink:#2b2b2b;
    --ink-soft:#4a4a4a;
    --paper:#ffffff;
    --backdrop:#eef0ec;
    --rule:#8c8c8c;
  }
  *{box-sizing:border-box;margin:0;padding:0}
  html,body{width:1200px;height:1178px;overflow:hidden}
  body{background:var(--backdrop);position:relative;font-family:"Source Sans 3",Arial,sans-serif;color:var(--ink)}

  .card{position:absolute;width:916px;height:524px;background:var(--paper);box-shadow:0 2px 6px rgba(0,0,0,.18);overflow:hidden}
  .card--front{left:30px;top:37px}
  .card--back{left:256px;top:618px;border:1px solid #cfcfcf}

  .brand{position:absolute;color:var(--green-dark);font-weight:600;text-align:center;line-height:1}
  .brand__mark{position:absolute;border-radius:50%;background:var(--green-light)}
  .brand__name{display:block;letter-spacing:1px}
  .brand__sub{display:block;letter-spacing:3px;text-transform:uppercase}

  .card--front .brand{left:258px;top:120px;width:400px}
  .card--front .brand__mark{width:64px;height:64px;left:168px;top:-100px}
  .card--front .brand__name{font-size:78px}
  .card--front .brand__sub{font-size:44px;margin-top:14px}

  .card--back .brand{left:52px;top:34px;width:240px}
  .card--back .brand__mark{width:38px;height:38px;left:100px;top:-20px}
  .card--back .brand__name{font-size:46px;margin-top:26px}
  .card--back .brand__sub{font-size:26px;margin-top:8px}

  .identity{position:absolute;right:498px;top:303px;text-align:right}
  .identity__name{font-size:32px;font-weight:700;color:var(--green-dark);line-height:1.1}
  .identity__title{font-size:25px;color:var(--ink-soft);margin-top:8px;line-height:1.1}
  .identity__address{font-size:22px;line-height:35px;margin-top:8px;white-space:nowrap}

  .divider{position:absolute;left:438px;top:313px;width:1.5px;height:144px;background:var(--rule)}

  .contacts{position:absolute;left:452px;top:308px;list-style:none}
  .contacts li{display:flex;align-items:center;height:40px;font-size:22px}
  .contacts svg{width:18px;height:18px;margin-right:8px;fill:var(--green-dark)}

  .bands{position:absolute;left:0;bottom:0;width:100%;height:37px}
  .band{position:absolute;top:0;height:37px}
  .band--left{left:0;width:296px;background:var(--green-dark)}
  .band--mid{left:309px;width:297px;background:var(--green-light)}
  .band--right{left:619px;width:297px;background:var(--green-dark)}

  .appt-title{position:absolute;left:81px;top:175px;font-family:"Cinzel",Georgia,serif;font-weight:600;font-size:32px;color:var(--green-dark);letter-spacing:1px}
  .field{position:absolute;font-size:24px;color:var(--ink-soft)}
  .dots{position:absolute;border-bottom:2px dotted #9a9a9a;height:0}
  .slot{position:absolute;width:164px;height:37px;border:1.5px solid #555;border-radius:5px}

  .days{position:absolute;right:22px;top:78px;list-style:none}
  .days li{display:flex;justify-content:flex-end;align-items:center;font-size:25px;font-weight:700;color:#333;position:absolute;right:0;white-space:nowrap}
  .days li span{display:inline-block;width:56px;height:32px;border:1.5px solid #555;border-radius:3px;margin-left:14px}

  .notice{position:absolute;left:78px;top:448px;font-size:25px;font-style:italic;color:#222;white-space:nowrap}
  .back-band{position:absolute;left:0;bottom:0;width:100%;height:12px;background:var(--green-dark)}
</style>
</head>
<body>

<section class="card card--front" aria-label="Business card front">
  <div class="brand">
    <span class="brand__mark"></span>
    <span class="brand__name">Brightwell</span>
    <span class="brand__sub">Dental Care</span>
  </div>

  <div class="identity">
    <p class="identity__name">Corwel T. Banfry</p>
    <p class="identity__title">DDS</p>
    <p class="identity__address">2730 W. Halvert Rd.<br>Ste. 7 Maple Hollow, OH 48391</p>
  </div>

  <div class="divider"></div>

  <ul class="contacts">
    <li><svg viewBox="0 0 24 24"><path d="M6.6 10.8a15.1 15.1 0 0 0 6.6 6.6l2.2-2.2a1 1 0 0 1 1-.25 11.4 11.4 0 0 0 3.6.57 1 1 0 0 1 1 1V20a1 1 0 0 1-1 1A17 17 0 0 1 3 4a1 1 0 0 1 1-1h3.5a1 1 0 0 1 1 1c0 1.25.2 2.45.57 3.57a1 1 0 0 1-.25 1z"/></svg>(419)555-0174</li>
    <li><svg viewBox="0 0 24 24"><path d="M7 3h8l2 2v4H7zM4 10h16a2 2 0 0 1 2 2v6h-4v3H6v-3H2v-6a2 2 0 0 1 2-2zm4 7v2h8v-2z"/></svg>(419)555-0189</li>
    <li><svg viewBox="0 0 24 24"><path d="M2 6h20v12H2zm2 2v.5l8 5 8-5V8l-8 5z"/></svg>info@BrightwellDentalCareMi.com</li>
    <li><svg viewBox="0 0 24 24"><path d="M12 2a10 10 0 1 0 0 20 10 10 0 0 0 0-20zm6.9 9h-3a15 15 0 0 0-1.3-5.6A8 8 0 0 1 18.9 11zM12 4c.9 1.2 1.8 3.6 2 7h-4c.2-3.4 1.1-5.8 2-7zM9.4 5.4A15 15 0 0 0 8.1 11h-3a8 8 0 0 1 4.3-5.6zM5.1 13h3a15 15 0 0 0 1.3 5.6A8 8 0 0 1 5.1 13zM12 20c-.9-1.2-1.8-3.6-2-7h4c-.2 3.4-1.1 5.8-2 7zm2.6-1.4a15 15 0 0 0 1.3-5.6h3a8 8 0 0 1-4.3 5.6z"/></svg>BrigthwellDentalCareMi.com</li>
  </ul>

  <div class="bands">
    <div class="band band--left"></div>
    <div class="band band--mid"></div>
    <div class="band band--right"></div>
  </div>
</section>

<section class="card card--back" aria-label="Business card back, appointment reminder">
  <div class="brand">
    <span class="brand__mark"></span>
    <span class="brand__name">Brightwell</span>
    <span class="brand__sub">Dental Care</span>
  </div>

  <h2 class="appt-title">YOUR APPOINTMENT</h2>

  <span class="field" style="left:83px;top:241px">Name :</span>
  <span class="dots" style="left:185px;top:268px;width:504px"></span>

  <span class="field" style="left:83px;top:301px">Date :</span>
  <span class="dots" style="left:185px;top:328px;width:166px"></span>
  <span class="field" style="left:359px;top:301px">Time :</span>
  <span class="dots" style="left:441px;top:328px;width:156px"></span>
  <span class="field" style="left:600px;top:301px">am / pm</span>

  <span class="field" style="left:83px;top:368px">Next Appointment</span>
  <span class="slot" style="left:328px;top:372px"></span>
  <span class="slot" style="left:530px;top:372px"></span>

  <ul class="days">
    <li style="top:0">MON<span></span></li>
    <li style="top:62px">TUE<span></span></li>
    <li style="top:125px">WED<span></span></li>
    <li style="top:189px">THU<span></span></li>
    <li style="top:245px">FRI<span></span></li>
    <li style="top:301px">SAT<span></span></li>
  </ul>

  <p class="notice">If you are unable to keep your appointment, kindly give 48 hours notice</p>
  <div class="back-band"></div>
</section>

</body>
</html>
```